Wordpress Design for a Digital Management Consulting Business

I need a simple Wordpress Design and someone to set it up for a new boutique management consulting business called Quillon Advisory that specialises in providing strategic advice to help grow digital businesses. It covers business strategy, marketing strategy, digital strategy, web product development, marketing campaigns, social, search, etc. From strategy to implementation.

URL is: quillonadvisory.com.au

My professional background is here: au.linkedin.com/in/hollyprenwick

Competitors: other boutique digital/marketing management consulting businesses in Australia

The logos, colours and fonts are attached.

I would like the site to convey a business that is Smart/intelligent, Contemporary, Progressive, Digital, Energetic, Friendly.

The objective of the site is to educate visitors about what Quillon Advisory does and encourage them to contact me for more information. It will be very light on content.

Target Market(s)

CEOs/Managing Directors, General Managers, Marketing Directors

Industry/Entity Type

Management Consulting

Font styles to use
Sans Serif

Colors
e34197
5c5c5c
000000

Requirements
Must have
• Site design requirements:
• Choose an appropriate Wordpress template, set it up for me and let me be able to edit it ongoing.
• It should use lots of images - these can be inspirational and not necessarily tied directly to the work
• Pink should feature, but not be the dominant colour.
• Site structure should be:
• 1. Home page - image led with horizontal navigation. Text beneath and images to describe the services.
• 2. About page - with space to write text and insert a picture of the Director
• 3. Services - with space to highlight services either as a list or graphically with text
• 4. Contact page - with space to write text and add email links, etc.
• Should have horizontal navigation
• It should have the flexibility to add another page
Nice to have
• Use the tree icon somehow in the design - consider in the background enlarged
• Use pink, grey, black from logo. Can introduce another complimentary colour if necessary.
• Can introduce another complimentary font to go with the logo font.
Should not have
• Use cliched business images and icons, eg. business suits, hand shakes, business men, business ties.

```html
<!DOCTYPE html>
<html lang="en">
<head>
<meta charset="utf-8">
<title>Quillon Advisory</title>
<link href="https://fonts.googleapis.com/css2?family=Open+Sans:wght@400;600;700&display=swap" rel="stylesheet">
<style>
:root{
  --pink:#e34197;
  --grey:#5c5c5c;
  --black:#000;
  --ink:#222;
  --muted:#777;
  --light:#f3f3f3;
  --footer:#0d0d0d;
}
*{box-sizing:border-box;margin:0;padding:0}
html,body{width:753px;height:1200px;overflow:hidden}
body{font-family:"Open Sans",Arial,sans-serif;background:#fff;color:var(--ink);position:relative}
.header{position:absolute;top:0;left:0;width:753px;height:50px;background:#fff;display:flex;align-items:center;justify-content:space-between;padding:0 30px}
.brand{display:flex;align-items:center;gap:8px}
.brand-dot{width:22px;height:22px;border-radius:50%;background:var(--pink)}
.brand-name{font-size:19px;font-weight:600;color:var(--grey);letter-spacing:.5px}
.nav{display:flex;gap:26px;list-style:none;font-size:8px;font-weight:600;letter-spacing:.4px}
.nav li{color:var(--grey)}
.nav li.active{color:var(--pink)}
.hero{position:absolute;top:50px;left:0;width:753px;height:255px;background:linear-gradient(100deg,#e9e3de 0%,#d9cfc8 45%,#b9aca6 70%,#8f827e 100%)}
.hero-text{position:absolute;top:78px;left:30px;width:240px}
.hero-title{font-size:24px;font-weight:400;color:#111;margin-bottom:6px}
.hero-copy{font-size:8px;line-height:1.45;color:#333}
.intro{position:absolute;top:318px;left:28px;width:696px}
.intro h2{font-size:11.5px;font-weight:600;color:var(--pink);margin-bottom:5px}
.intro p{font-size:7.6px;line-height:1.5;color:var(--grey)}
.intro-rule{position:absolute;top:400px;left:28px;width:696px;height:1px;background:#e2e2e2}
.section-title{font-size:23px;font-weight:400;color:#111}
.services{position:absolute;top:428px;left:28px;width:696px}
.services .section-title{margin-bottom:14px}
.cards{display:flex;justify-content:space-between}
.card{width:220px}
.card-photo{width:220px;height:92px;margin-bottom:10px}
.card h3{font-size:12px;font-weight:400;color:var(--pink);margin-bottom:4px}
.card p{font-size:7px;line-height:1.45;color:var(--muted);margin-bottom:6px}
.read{font-size:7.5px;font-weight:600;color:#111}
.whatwedo{position:absolute;top:688px;left:0;width:753px;height:300px;background:linear-gradient(#e9e9e9,#f7f7f7 40%,#fff)}
.whatwedo .section-title{position:absolute;top:28px;left:28px}
.wcards{position:absolute;top:78px;left:28px;width:696px;display:flex;justify-content:space-between}
.wcard{width:220px}
.wcard-photo{width:220px;height:92px;border:2px solid var(--pink);margin-bottom:10px}
.wcard h3{font-size:14px;font-weight:400;color:#111;line-height:1.2;margin-bottom:5px}
.wcard p{font-size:7px;line-height:1.45;color:var(--muted);margin-bottom:7px}
.btn{display:inline-block;background:var(--pink);color:#fff;font-size:7.5px;padding:4px 9px}
.footer{position:absolute;top:1005px;left:0;width:753px;height:163px;background:var(--footer);color:#ccc}
.footer h4{font-size:17px;font-weight:400;color:#fff;margin-bottom:10px}
.fcol{position:absolute;top:18px}
.flist{list-style:none;font-size:6.8px;line-height:1.8}
.flist li::before{content:"›";color:var(--pink);margin-right:5px}
.flist-pair{display:flex;gap:40px}
.contact-line{display:flex;align-items:center;gap:6px;font-size:6.8px;margin-bottom:8px}
.contact-line svg{flex:none}
.socials{display:flex;gap:6px;margin-top:6px}
.social{width:15px;height:15px;border-radius:50%;border:1px solid #888}
.copybar{position:absolute;top:1168px;left:0;width:753px;height:32px;background:var(--pink);color:#fff;font-size:7px;display:flex;align-items:center;justify-content:center}
</style>
</head>
<body>
<header class="header">
  <div class="brand"><span class="brand-dot"></span><span class="brand-name">Quillon Advisory</span></div>
  <ul class="nav">
    <li class="active">HOME</li><li>SERVICES</li><li>ABOUT</li><li>CLIENTS</li><li>CONTACT US</li>
  </ul>
</header>

<section class="hero" role="img" aria-label="Photo of a hand touching a tablet screen in soft light">
  <div class="hero-text">
    <h1 class="hero-title">Quillon Advisory</h1>
    <p class="hero-copy">Boutique management consulting company working digital businesses across business product and marketing strategy.</p>
  </div>
</section>

<section class="intro">
  <h2>Quillon Advisory is a boutique management consulting company.</h2>
  <p>Quillon Advisory was founded in July 2014 and has provided strategic advice to a range of large corporate clients and small entrepreneurial businesses around Australia and internationally. The face of Quillon Advisory is Holly Prenwick who's 15 years digital and strategic experience working Holly draws on experts as projects require.</p>
</section>
<div class="intro-rule"></div>

<section class="services">
  <h2 class="section-title">Our Services</h2>
  <div class="cards">
    <article class="card">
      <div class="card-photo" role="img" aria-label="Photo of a hand on a tablet showing charts" style="background:linear-gradient(120deg,#dfe7ef,#8fb4d6 60%,#3f6f9e)"></div>
      <h3>Digital Strategy</h3>
      <p>Lorem ipsum dolor sit amet, consectetur adipisici elit, sed eiusmod tempor incidunt ut labore et dolore magna aliqua...</p>
      <span class="read">Read more..</span>
    </article>
    <article class="card">
      <div class="card-photo" role="img" aria-label="Photo of a person working at a desk" style="background:linear-gradient(120deg,#f1f1f1,#c9c9c9 55%,#6d6d6d)"></div>
      <h3>Marketing Strategy</h3>
      <p>Lorem ipsum dolor sit amet, consectetur adipisici elit, sed eiusmod tempor incidunt ut labore et dolore magna aliqua...</p>
      <span class="read">Read more..</span>
    </article>
    <article class="card">
      <div class="card-photo" role="img" aria-label="Photo of digital screens and devices" style="background:linear-gradient(120deg,#1d2a3a,#3d5a7a 55%,#9fb3c8)"></div>
      <h3>Digital Transformation</h3>
      <p>Lorem ipsum dolor sit amet, consectetur adipisici elit, sed eiusmod tempor incidunt ut labore et dolore magna aliqua...</p>
      <span class="read">Read more..</span>
    </article>
  </div>
</section>

<section class="whatwedo">
  <h2 class="section-title">What we do</h2>
  <div class="wcards">
    <article class="wcard">
      <div class="wcard-photo" role="img" aria-label="Photo of a team discussing around a table" style="background:linear-gradient(120deg,#e8e2dc,#b9a99a 55%,#6f6259)"></div>
      <h3>Strategic Thinking</h3>
      <p>Lorem Ipsum has been the industry's standard dummy text ever since, sed eiusmod tempor.</p>
      <span class="btn">Read more..</span>
    </article>
    <article class="wcard">
      <div class="wcard-photo" role="img" aria-label="Photo of charts and documents on a desk" style="background:linear-gradient(120deg,#f4f4f4,#cfd6dc 55%,#8a97a3)"></div>
      <h3>Analytical Approach</h3>
      <p>Lorem Ipsum has been the industry's standard dummy text, consectetur adipisici elit, sed eiusmod tempor.</p>
      <span class="btn">Read more..</span>
    </article>
    <article class="wcard">
      <div class="wcard-photo" role="img" aria-label="Photo of colleagues working together at laptops" style="background:linear-gradient(120deg,#dfe6ec,#9fb0bf 55%,#55626e)"></div>
      <h3>End to end project<br>Management</h3>
      <p>Lorem Ipsum has been the industry's standard dummy text.</p>
      <span class="btn">Read more..</span>
    </article>
  </div>
</section>

<footer class="footer">
  <div class="fcol" style="left:28px">
    <h4>Links</h4>
    <ul class="flist"><li>Home</li><li>Our Services</li><li>About Us</li><li>Clients</li><li>Contact Us</li></ul>
  </div>
  <div class="fcol" style="left:186px">
    <h4>Services</h4>
    <div class="flist-pair">
      <ul class="flist"><li>Business Strategy</li><li>Digital Strategy</li><li>Marketing Strategy</li><li>Product Strategy</li><li>Marketing Campaigns</li></ul>
      <ul class="flist"><li>Product Management</li><li>Digital Marketing</li><li>Data/CRM Strategy</li><li>Content Marketing</li><li>New Product Launches</li></ul>
    </div>
  </div>
  <div class="fcol" style="left:505px">
    <h4>Contact Us</h4>
    <div class="contact-line">
      <svg width="10" height="10" viewBox="0 0 24 24"><path fill="#ccc" d="M6.6 10.8a15 15 0 0 0 6.6 6.6l2.2-2.2a1 1 0 0 1 1-.25 11.4 11.4 0 0 0 3.6.57 1 1 0 0 1 1 1V20a1 1 0 0 1-1 1A17 17 0 0 1 3 4a1 1 0 0 1 1-1h3.5a1 1 0 0 1 1 1c0 1.25.2 2.45.57 3.57a1 1 0 0 1-.25 1z"/></svg>
      <span>Holly Prenwick 0400 118 274</span>
    </div>
    <div class="contact-line">
      <svg width="10" height="10" viewBox="0 0 24 24"><rect x="2" y="5" width="20" height="14" fill="none" stroke="#ccc" stroke-width="2"/><path d="M2 5l10 8 10-8" fill="none" stroke="#ccc" stroke-width="2"/></svg>
      <span>holly@quillonadvisory.com.au</span>
    </div>
    <div class="socials"><span class="social"></span><span class="social"></span><span class="social"></span><span class="social"></span></div>
  </div>
</footer>
<div class="copybar">© 2015 Copyright Quillon Advisory. All Rights Reserved</div>
</body>
</html>
```